Brindlewick Solutions Ltd

I'd like to create a company letterhead for the attached logo in word format.

I'd like to emphasis the icon in large translucent state from the left corner and ensure that the letterhead colouring matches the colour palette of the current logo with a contrast so it's clear to see. I've attached a copy of our sister company page on the app for reference.

```html
<!DOCTYPE html>
<html lang="en">
<head>
<meta charset="utf-8">
<title>Brindlewick Solutions Ltd — Letterhead</title>
<link rel="stylesheet" href="https://fonts.googleapis.com/css2?family=Arimo:wght@400;700&family=Questrial&family=Mulish:wght@700&display=swap">
<style>
  :root {
    --backdrop: #e2e2e2;
    --paper: #ffffff;
    --brand: #06bfa7;
    --brand-faint: #eef8f8;
    --ink: #555555;
    --ink-soft: #9a9a9a;
    --rule: #c8c8c8;
  }
  * { box-sizing: border-box; margin: 0; padding: 0; }
  html, body {
    width: 1200px; height: 1200px; overflow: hidden;
    background: var(--backdrop);
  }
  .letterhead {
    position: absolute; left: 197px; top: 30px;
    width: 806px; height: 1140px;
    background: var(--paper);
    overflow: hidden;
    font-family: "Arimo", Arial, sans-serif;
    color: var(--ink);
  }
  .brand-watermark {
    position: absolute; left: 284px; top: 618px;
    width: 524px; height: 524px; border-radius: 50%;
    background: var(--brand-faint);
  }
  .brand {
    position: absolute; left: 72px; top: 62px;
    display: flex; align-items: center; gap: 12px;
    color: var(--brand); font-weight: 400;
  }
  .brand-dot {
    width: 72px; height: 72px; border-radius: 50%;
    background: var(--brand);
  }
  .brand-name { font-size: 38px; line-height: 1; }
  .brand-tagline { font-size: 10px; letter-spacing: 7px; margin-top: 6px; }
  .contact {
    position: absolute; left: 591px; top: 38px;
    font-size: 12.5px; line-height: 1.15; color: var(--ink-soft);
  }
  .contact-address { margin-bottom: 10px; }
  .contact-line { display: flex; align-items: center; gap: 6px; height: 18px; }
  .contact-line svg { width: 11px; height: 11px; flex: none; }
  .header-rule {
    position: absolute; left: 72px; top: 143px;
    width: 662px; height: 1px; background: var(--rule);
  }
  .salutation {
    position: absolute; left: 74px; top: 349px;
    font-family: "Questrial", "Century Gothic", sans-serif;
    font-size: 19px; font-weight: 700; color: var(--ink);
    -webkit-text-stroke: 0.4px var(--ink);
  }
  .letter-body {
    position: absolute; left: 73px; top: 401px; width: 666px;
    font-size: 13.6px; line-height: 16.5px;
  }
  .letter-body p { margin-bottom: 14px; }
  .closing {
    position: absolute; left: 74px; top: 744px;
    font-family: "Questrial", "Century Gothic", sans-serif;
    font-size: 11px; font-weight: 700;
    -webkit-text-stroke: 0.3px var(--ink);
  }
  .signatory {
    position: absolute; left: 93px; top: 799px;
    font-family: "Mulish", sans-serif; font-size: 19px;
    letter-spacing: -1px; color: var(--ink);
  }
</style>
</head>
<body>
  <main class="letterhead">
    <div class="brand-watermark"></div>

    <header>
      <div class="brand">
        <div class="brand-dot"></div>
        <div>
          <div class="brand-name">Brindlewick</div>
          <div class="brand-tagline">SOLUTIONS LTD</div>
        </div>
      </div>

      <address class="contact" style="font-style:normal">
        <div class="contact-address">Your address, city<br>state, ZIP 0000</div>
        <div class="contact-line">
          <svg viewBox="0 0 12 12" aria-hidden="true"><path fill="#06bfa7" d="M2.5 1 4.5 3 3.5 4.5c.8 1.7 2.2 3.1 4 4L9 7.5l2 2-1.5 1.5C5 10.5 1.5 7 1 2.5Z"/></svg>
          123-456-0199
        </div>
        <div class="contact-line">
          <svg viewBox="0 0 12 12" aria-hidden="true"><rect x="0.5" y="2.5" width="11" height="7.5" fill="#06bfa7"/><path d="M0.8 2.8 6 7l5.2-4.2" fill="none" stroke="#fff" stroke-width="1"/></svg>
          hello@brindlewick.example
        </div>
        <div class="contact-line">
          <svg viewBox="0 0 12 12" aria-hidden="true"><circle cx="6" cy="6" r="5.5" fill="#06bfa7"/><path d="M0.5 6h11M6 .5c-2.5 3-2.5 8 0 11M6 .5c2.5 3 2.5 8 0 11" fill="none" stroke="#fff" stroke-width="0.8"/></svg>
          www.brindlewick.example
        </div>
      </address>
      <div class="header-rule"></div>
    </header>

    <h1 class="salutation">Dear Mr. Halvorsen,</h1>

    <section class="letter-body">
      <p>Lorem ipsum dolor sit amet, consectetuer adipiscing elit, sed diam nonmmy nibh euismod tincidunt ut laor eet dolore magna aliquam erat volutpat. Ut wisi enim ad minim veniam, quis nostrud exerci tationmcorper suscipit lobortis nisl ut aliquip ex ea commodo consequat. Duis autem vel eum iriure dolor in hendrerit in vulputate velit esse molestie consequat, vel illum dolore eu feugiat</p>
      <p>Rorem ipsum dolor sit amet, consectetuer adipiscing elit, sed diam nonmmy nibh euismod tincidunt ut laor eet dolore magna aliquam erat volutpat. Ut wisi enim ad minim veniam, quis nostrud exerci tationmcorper suscipit lobortis nisl ut aliquip ex ea commodo consequat. Duis autem vel eum iriure dolor in hendrerit in vulputate velit esse molest</p>
      <p>Dorem ipsum dolor sit amet, consectetuer adipiscing elit, sed diam nonmmy nibh euismod tincidunt ut laor eet dolore magna aliquam erat volutpat. Ut wisi enim ad minim veniam, quis nostrud exerci tationmcorper suscipit lobortis nisl ut aliquip ex ea commodo consequat. Duis autem vel eum iriure dolor in hendrerit in suscipit lobortis nisl ut aliquip ex ea commodo consequat. Duis autem vel eum iriure dolor in hendrerit in vulputate velit esse molestie consequat, vel illum</p>
      <p>Sorem ipsum dolor sit amet, consectetuer adipiscing elit, sed diam nonmmy nibh euismod tincidunt ut laor eet dolore magna aliquam erat volutpat. Ut wisi enim ad minim veniam, quis nostrud exerci tationmcorper suscipit lobortis nisl ut aliquip ex ea commodo consequat. Duis autem vel eum iriure dolor in</p>
    </section>

    <p class="closing">Sincerely,</p>
    <p class="signatory">Corwin Aldous</p>
  </main>
</body>
</html>
```